We provide Professional DJ Service in different genres of music ranging from Latin to Hip/Hop R&B/TOP 40 etc...we also help promote DJ/Music/Artists events Internationally. I am looking for the main color of my business to be fluorescent lime green with some traces of 'smurf' blue. Maybe military feel attached to it as well as I am active duty military and all of my DJ's are either active or retired. That would be our main focus. We can do anything from Formal military balls to backyard parties We are also mobile and can be hired by local clubs/pubs/bars.

Target Market(s)

Military Community/Events/ Local nightclubs/pubs/bars looking to hire professional DJ's.

Industry/Entity Type

Entertainment

Contact Information for Business Card

Valdora Entertainment (Professional DJ Service/Event Promoter)/email:brenvaldora@mailnest.example/ Chatterbook logo with address or scan directly to my page. (Chatterbook-search Valdora Entertainment) Tomas 'DJ Grillo' Valdora. Owner/DJ/Promoter

Font styles to use
Serif

Colors
acd136
33a6d7

Requirements
Must have
• Looking for on back of card Chatterbook logo and scanbar leading directly to my CB page...if not possible then Chatterbook.example search Valdora Entertainment (or both).
Nice to have
• The attachment that I sent has my logo that I would like to use, however it is not a finished product. Is this only for business cards layout or also to spruce up or make my logo better? It's the Valdora

```html
<!DOCTYPE html>
<html lang="en">
<head>
<meta charset="utf-8">
<title>Valdora Entertainment – Business Card</title>
<link rel="stylesheet" href="https://fonts.googleapis.com/css2?family=PT+Serif:wght@400;700&display=swap">
<style>
  :root {
    --lime: #acd136;
    --blue: #33a6d7;
    --card: #0b0b0b;
    --ink: #ffffff;
    --stage: #2e2e2e;
    --divider: #1f3b4a;
    --social: #3b5a9a;
  }
  * { box-sizing: border-box; margin: 0; padding: 0; }
  html, body { width: 1200px; height: 900px; overflow: hidden; }
  body {
    background: var(--stage);
    font-family: "PT Serif", serif;
    display: flex;
    align-items: center;
    justify-content: center;
    gap: 60px;
  }
  .card {
    position: relative;
    width: 500px;
    height: 286px;
    background: var(--card);
    border-radius: 18px;
    overflow: hidden;
  }
  .brand-mark {
    position: absolute;
    width: 140px;
    height: 140px;
    border-radius: 50%;
    background: var(--blue);
    display: flex;
    align-items: center;
    justify-content: center;
    text-align: center;
    color: var(--card);
    font-weight: 700;
    font-size: 14px;
    line-height: 1.25;
    padding: 0 14px;
    text-transform: uppercase;
  }

  /* Front */
  .card-front .brand-mark { left: 36px; top: 80px; }
  .card-front .divider {
    position: absolute;
    left: 206px; top: 40px;
    width: 1px; height: 160px;
    background: linear-gradient(var(--card), var(--divider), var(--card));
  }
  .contact { position: absolute; left: 226px; top: 62px; color: var(--ink); }
  .contact .name { font-size: 18px; font-weight: 700; color: var(--lime); white-space: nowrap; }
  .contact .name .surname { color: var(--blue); }
  .contact .role { font-size: 13px; margin-top: 2px; }
  .contact .email {
    display: flex; align-items: center; gap: 8px;
    font-size: 13px; margin-top: 18px; white-space: nowrap;
  }
  .social {
    position: absolute; left: 226px; top: 200px;
    display: flex; align-items: center; gap: 8px;
    color: var(--ink); font-size: 13px; font-weight: 700;
  }
  .social .square { width: 30px; height: 30px; background: var(--social); border-radius: 3px; }

  /* Back */
  .card-back .brand-mark { left: 190px; top: 40px; }
  .card-back .rule-top {
    position: absolute; left: 340px; right: 14px; top: 108px;
    height: 1px; background: var(--lime);
  }
  .tagline {
    position: absolute; left: 14px; right: 24px; top: 196px;
    display: flex; align-items: center; gap: 8px;
    font-size: 15px; font-weight: 700; white-space: nowrap;
  }
  .tagline::before { content: ""; flex: 1; height: 1px; background: var(--lime); }
  .tagline .lead { color: var(--lime); }
  .tagline .rest { color: var(--blue); }
  .card-back .social { left: auto; right: 24px; top: 238px; font-size: 12px; }
  .card-back .social .square { width: 20px; height: 20px; }
</style>
</head>
<body>
  <section class="card card-front">
    <div class="brand-mark">Valdora Entertainment</div>
    <div class="divider"></div>
    <div class="contact">
      <p class="name">Tomas 'DJ Grillo' <span class="surname">Valdora</span></p>
      <p class="role">Owner/DJ/Promoter</p>
      <p class="email">
        <svg width="11" height="8" viewBox="0 0 11 8" aria-hidden="true">
          <rect width="11" height="8" fill="#acd136"/>
          <path d="M0 0 L5.5 4.5 L11 0" stroke="#0b0b0b" stroke-width="1" fill="none"/>
        </svg>
        brenvaldora@mailnest.example
      </p>
    </div>
    <div class="social"><span class="square"></span>Chatterbook</div>
  </section>

  <section class="card card-back">
    <div class="brand-mark">Valdora Entertainment</div>
    <div class="rule-top"></div>
    <p class="tagline"><span><span class="lead">Professional DJ </span><span class="rest">Service/Event Promoter</span></span></p>
    <div class="social"><span class="square"></span>Chatterbook</div>
  </section>
</body>
</html>
```